Redesign Website - Current one too plain

The description is in the uploaded file. Please let me know if you need any more information. I'd prefer it if someone could implement the design to a WordPress site but the best design will win, regardless.
I would like the forms to look nice as well
UPDATE:
I don't think we can use the images that I provided, I think they make the site look a bit 'cheap' and I really don't know how to replace them. One thought I have had is to make the "Simple, Unique, Effective" a second feature on the right side of the page with the search on the left
Target Market(s)
Small companies, private sellers of cars and people who rent their caravan/holiday home out
Industry/Entity Type
Advertising
Number of Pages Required
3 page
Colors
Designer to choose colors to be used in the design.
Look and feel
Each slider illustrates characteristics of the customer's brand and the style your logo design should communicate.

```html
<!DOCTYPE html>
<html lang="en">
<head>
<meta charset="utf-8">
<title>KODRA – Simple, Unique, Effective Advertising</title>
<link rel="stylesheet" href="https://fonts.googleapis.com/css2?family=Open+Sans:wght@400;600;700&family=Poppins:wght@400;500;600;700&display=swap">
<style>
:root{
  --lime:#e4ff00;
  --lime-deep:#d6ef00;
  --blue:#0043a8;
  --ink:#111111;
  --text:#333333;
  --grey-dark:#4a4a4a;
  --grey-band:#ececee;
  --white:#ffffff;
  --black:#000000;
}
*{box-sizing:border-box;margin:0;padding:0}
html,body{width:1200px;height:2649px;overflow:hidden;background:var(--white)}
body{font-family:"Open Sans",sans-serif;color:var(--text)}
.page{position:relative;width:1200px;height:2649px;overflow:hidden}
.abs{position:absolute}

/* header */
.brand{left:98px;top:12px;display:flex;align-items:center;gap:14px;font-family:"Open Sans",sans-serif;font-weight:700;font-size:42px;letter-spacing:9px;color:var(--ink)}
.brand-mark{width:42px;height:42px;border-radius:50%;background:var(--ink)}
.nav{right:98px;top:20px;display:flex;align-items:center;gap:36px;font-size:16px;color:var(--text)}
.nav a{color:inherit;text-decoration:none}
.nav .current{font-weight:600;text-decoration:underline;text-underline-offset:5px;color:var(--ink)}
.btn-login{background:var(--lime);color:var(--ink)!important;font-weight:600;font-size:18px;width:120px;height:46px;display:flex;align-items:center;justify-content:center;box-shadow:0 3px 6px rgba(0,0,0,.15)}

/* hero */
.hero{left:0;top:85px;width:1200px;height:600px;border-radius:70px;overflow:hidden;background:linear-gradient(100deg,#575757 0%,#6a6a6a 45%,#5a5a5a 100%)}
.hero-vehicles{left:400px;top:95px;width:705px;height:420px;border-radius:30px;background:radial-gradient(ellipse at 55% 40%,#c9c7bf 0%,#9a9893 45%,rgba(110,110,110,0) 75%)}
.plate{background:var(--lime);color:var(--ink);font-size:15px;font-weight:600;width:34px;height:32px;display:flex;align-items:center;justify-content:center}
.code{left:96px;top:160px;font-family:"Poppins",sans-serif;font-weight:700;font-size:130px;line-height:1;color:var(--lime);letter-spacing:2px}
.chev{width:22px;height:12px}
.options{left:98px;top:332px;display:flex;gap:20px;color:var(--white);font-size:18px;font-weight:500}
.options span::before{content:"";display:inline-block;width:10px;height:10px;border-radius:50%;background:var(--white);margin-right:6px;vertical-align:1px}
.btn-search{left:99px;top:375px;width:120px;height:46px;background:var(--lime);color:var(--ink);font-size:18px;font-weight:500;display:flex;align-items:center;justify-content:center}

/* features */
.feature-art{left:0;top:740px}
.feature{width:260px;text-align:center}
.feature h3{font-size:22px;font-weight:600;color:var(--ink);margin-bottom:8px}
.feature p{font-size:15px;line-height:31px;color:var(--text)}

/* about */
.about{left:0;top:1293px;width:1200px;height:444px;background:linear-gradient(115deg,#ececee 0%,#ececee 55%,#e6e6e8 55%,#f1f1f3 100%)}
.about h2{position:absolute;top:52px;width:100%;text-align:center;font-size:32px;font-weight:600;color:var(--ink);letter-spacing:.5px}
.about p{position:absolute;top:100px;left:106px;width:988px;text-align:center;font-size:15px;line-height:31px;color:var(--text)}
.btn-advertise{position:absolute;left:472px;top:336px;width:256px;height:47px;background:var(--blue);color:var(--white);font-size:18px;font-weight:600;display:flex;align-items:center;justify-content:center}

/* testimonials */
.testi-title{top:1790px;width:1200px;text-align:center;font-size:32px;font-weight:600;color:var(--ink);letter-spacing:.5px}
.card{width:308px;height:190px;top:1898px;background:var(--white);border-radius:14px;box-shadow:0 4px 16px rgba(0,0,0,.12);border-top:3px solid var(--blue)}
.card.grey{border-top-color:var(--grey-dark)}
.card p{position:absolute;top:66px;left:20px;right:20px;text-align:center;font-size:14px;line-height:26px;color:var(--text)}
.card::after{content:"";position:absolute;left:144px;bottom:-9px;width:18px;height:18px;background:var(--white);transform:rotate(45deg)}
.avatar{width:90px;height:90px;border-radius:50%;background:radial-gradient(circle at 50% 40%,#d8cfc6 0%,#a89a8d 60%,#8a7e73 100%);border:2px solid var(--white);top:1854px}
.badge{width:24px;height:24px;border-radius:50%;background:var(--white);border:2px solid #dadada;top:1922px}
.reviewer{top:2113px;display:flex;align-items:center;gap:22px;font-size:15px;font-weight:600;color:var(--ink)}
.stars{color:#f4c400;font-size:14px;letter-spacing:1px}

/* footer */
.footer{left:0;top:2205px;width:1200px;height:444px;background:var(--black);color:var(--white);font-family:"Poppins",sans-serif}
.footer h4{position:absolute;font-size:26px;font-weight:600;top:50px}
.links{position:absolute;left:98px;top:95px;list-style:none;font-size:15px;line-height:31px}
.links li{display:flex;align-items:center;gap:12px}
.links svg{width:15px;height:12px}
.social{position:absolute;left:98px;top:277px;display:flex;gap:6px}
.social span{width:31px;height:31px;border-radius:50%;border:1.5px solid var(--white)}
.vsep{position:absolute;top:88px;height:240px;border-left:1px dashed #888}
.contact-item{position:absolute;left:355px;display:flex;gap:10px}
.ci-icon{width:35px;height:35px;border-radius:50%;border:1.5px solid var(--white);display:flex;align-items:center;justify-content:center;flex:none}
.ci-icon svg{width:16px;height:16px}
.contact-item strong{display:block;font-size:18px;font-weight:600;line-height:30px}
.contact-item span{font-size:16px;line-height:30px}
.hsep{position:absolute;left:355px;width:241px;border-top:1px dashed #888}
.field{position:absolute;left:716px;width:352px;height:40px;border:1.5px solid var(--white);font-size:15px;padding:0 12px;display:flex;align-items:center;color:var(--white)}
.btn-submit{position:absolute;left:716px;top:260px;width:352px;height:39px;background:var(--lime);color:var(--ink);font-size:17px;font-weight:600;display:flex;align-items:center;justify-content:center}
.rule{position:absolute;left:98px;top:389px;width:1002px;border-top:1px solid #bbb}
.copy{position:absolute;top:405px;width:1200px;text-align:center;font-size:15px}
</style>
</head>
<body>
<div class="page">

  <!-- Header -->
  <div class="abs brand"><span class="brand-mark"></span>KODRA</div>
  <nav class="abs nav">
    <a class="current" href="#">Home</a>
    <a href="#">Advertise</a>
    <a href="#">Contact</a>
    <a href="#">Register</a>
    <a class="btn-login" href="#">Login</a>
  </nav>

  <!-- Hero -->
  <section class="abs hero" role="img" aria-label="Dimmed office interior background photo">
    <div class="abs hero-vehicles" role="img" aria-label="Photo of a static caravan, an SUV and a van"></div>
    <div class="abs plate" style="left:698px;top:196px">A8</div>
    <div class="abs plate" style="left:487px;top:392px">X3</div>
    <div class="abs plate" style="left:860px;top:424px">F7</div>

    <svg class="abs chev" style="left:127px;top:148px" viewBox="0 0 22 12"><polyline points="1,11 11,1 21,11" fill="none" stroke="#fff" stroke-width="2"/></svg>
    <svg class="abs chev" style="left:215px;top:148px" viewBox="0 0 22 12"><polyline points="1,11 11,1 21,11" fill="none" stroke="#fff" stroke-width="2"/></svg>
    <div class="abs code">A1</div>
    <svg class="abs chev" style="left:127px;top:298px" viewBox="0 0 22 12"><polyline points="1,1 11,11 21,1" fill="none" stroke="#fff" stroke-width="2"/></svg>
    <svg class="abs chev" style="left:215px;top:298px" viewBox="0 0 22 12"><polyline points="1,1 11,11 21,1" fill="none" stroke="#fff" stroke-width="2"/></svg>

    <div class="abs options"><span>car</span><span>caravan</span><span>company</span></div>
    <div class="abs btn-search">Search</div>
  </section>

  <!-- Features -->
  <svg class="abs feature-art" width="1200" height="360" viewBox="0 740 1200 360">
    <defs>
      <filter id="soft" x="-30%" y="-30%" width="160%" height="160%"><feDropShadow dx="0" dy="6" stdDeviation="8" flood-opacity=".18"/></filter>
    </defs>
    <!-- arcs -->
    <path d="M183 890 A139 139 0 0 0 461 890 L418 890 A96 96 0 0 1 226 890 Z" fill="#dcf200"/>
    <path d="M461 890 A139 139 0 0 1 739 890 L696 890 A96 96 0 0 0 504 890 Z" fill="#4a4a4a"/>
    <path d="M739 890 A139 139 0 0 0 1017 890 L974 890 A96 96 0 0 1 782 890 Z" fill="#0043a8"/>
    <!-- stems -->
    <line x1="322" y1="1029" x2="322" y2="1075" stroke="#dcf200" stroke-width="3"/>
    <circle cx="322" cy="1080" r="12" fill="#dcf200"/>
    <line x1="600" y1="985" x2="600" y2="1075" stroke="#4a4a4a" stroke-width="3"/>
    <circle cx="600" cy="1080" r="12" fill="#4a4a4a"/>
    <line x1="877" y1="1029" x2="877" y2="1075" stroke="#0043a8" stroke-width="3"/>
    <circle cx="877" cy="1080" r="12" fill="#0043a8"/>
    <!-- discs -->
    <circle cx="322" cy="890" r="95" fill="#fff" filter="url(#soft)"/>
    <circle cx="600" cy="890" r="95" fill="#fff" filter="url(#soft)"/>
    <circle cx="877" cy="890" r="95" fill="#fff" filter="url(#soft)"/>
    <!-- simple: gears -->
    <g fill="none" stroke="#c9dc00" stroke-width="2.5">
      <circle cx="297" cy="865" r="14"/><circle cx="297" cy="865" r="6"/>
      <circle cx="348" cy="865" r="14"/><circle cx="348" cy="865" r="6"/>
      <circle cx="322" cy="907" r="20"/>
      <polyline points="312,907 320,915 333,899"/>
    </g>
    <!-- unique: people with star -->
    <g fill="none" stroke="#555" stroke-width="2.5">
      <circle cx="578" cy="876" r="8"/><circle cx="622" cy="876" r="8"/><circle cx="600" cy="888" r="9"/>
      <path d="M557 913 v-10 a10 10 0 0 1 10 -10 h8"/>
      <path d="M643 913 v-10 a10 10 0 0 0 -10 -10 h-8"/>
      <path d="M582 918 v-8 a12 12 0 0 1 12 -12 h12 a12 12 0 0 1 12 12 v8 z"/>
      <polygon points="600,858 603,866 611,866 605,871 607,879 600,874 593,879 595,871 589,866 597,866"/>
    </g>
    <!-- effective: gears + bulb -->
    <g fill="none" stroke="#0043a8" stroke-width="2.5">
      <circle cx="854" cy="905" r="16"/><circle cx="854" cy="905" r="7"/>
      <circle cx="899" cy="920" r="12"/><circle cx="899" cy="920" r="5"/>
      <path d="M842 880 a30 30 0 0 1 38 -28"/><polyline points="874,848 881,852 876,858"/>
      <path d="M905 878 a11 11 0 1 0 -12 0 v8 h12 z"/>
      <line x1="895" y1="892" x2="903" y2="892"/>
      <path d="M922 880 a40 40 0 0 1 -8 36"/>
    </g>
  </svg>

  <div class="abs feature" style="left:192px;top:1110px"><h3>Simple</h3><p>create&nbsp; your advert and<br>display your code</p></div>
  <div class="abs feature" style="left:470px;top:1110px"><h3>Unique</h3><p>customers find you by an<br>easy-to-remember code</p></div>
  <div class="abs feature" style="left:746px;top:1110px"><h3>Effective</h3><p>customers are directed to you<br>and not a list of your<br>competitors</p></div>

  <!-- About -->
  <section class="abs about">
    <h2>ABOUT KODRA</h2>
    <p>Sed ut perspiciatis unde omnis iste natus error sit voluptatem accusantium doloremque laudantium, totam rem aperiam, eaque ipsa quae ab illo inventore veritatis et quasi architecto beatae vitae dicta sunt explicabo. Nemo enim ipsam voluptatem quia voluptas sit aspernatur aut odit aut fugit, sed quia consequuntur magni dolores eos qui ratione voluptatem sequi nesciunt. Neque porro quisquam est, qui dolorem ipsum quia dolor sit amet, consectetur, adipisci velit, sed quia non numquam eius modi tempora incidunt ut labore et dolore magnam aliquam quaerat voluptatem. Ut enim ad minima veniam, quis nostrum exercitationem ullam corporis suscipit laboriosam, nisi ut aliquid ex ea commodi consequatur? Quis autem vel eum iure reprehenderit qui in ea voluptate velit esse quam nihil molestiae consequatur, vel illum qui dolorem eum fugiat quo voluptas nulla pariatur?</p>
    <div class="btn-advertise">Advertise your company</div>
  </section>

  <!-- Testimonials -->
  <h2 class="abs testi-title">CLIENT TESTIMONIALS</h2>

  <div class="abs card" style="left:112px"><p>Sed ut perspiciatis unde omnis iste natus error sit voluptatem accusantium doloremque laudantium, totam rem aperiam, eaque ipsa</p></div>
  <div class="abs card grey" style="left:445px"><p>Sed ut perspiciatis unde omnis iste natus error sit voluptatem accusantium doloremque laudantium, totam rem aperiam, eaque ipsa</p></div>
  <div class="abs card" style="left:778px"><p>Sed ut perspiciatis unde omnis iste natus error sit voluptatem accusantium doloremque laudantium, totam rem aperiam, eaque ipsa</p></div>

  <div class="abs avatar" style="left:221px" role="img" aria-label="Portrait photo of a client"></div>
  <div class="abs avatar" style="left:554px" role="img" aria-label="Portrait photo of a client"></div>
  <div class="abs avatar" style="left:887px" role="img" aria-label="Portrait photo of a client"></div>
  <div class="abs badge" style="left:277px"></div>
  <div class="abs badge" style="left:610px"></div>
  <div class="abs badge" style="left:943px"></div>

  <div class="abs reviewer" style="left:190px">Sam Rowe <span class="stars">★★★★★</span></div>
  <div class="abs reviewer" style="left:523px">Sam Rowe <span class="stars">★★★★★</span></div>
  <div class="abs reviewer" style="left:856px">Sam Rowe <span class="stars">★★★★★</span></div>

  <!-- Footer -->
  <footer class="abs footer">
    <h4 style="left:98px">Quick Links</h4>
    <ul class="links">
      <li><svg viewBox="0 0 15 12"><path d="M0 6h10M6 1l6 5-6 5" stroke="#fff" stroke-width="2.4" fill="none"/></svg>Home</li>
      <li><svg viewBox="0 0 15 12"><path d="M0 6h10M6 1l6 5-6 5" stroke="#fff" stroke-width="2.4" fill="none"/></svg>Advertise</li>
      <li><svg viewBox="0 0 15 12"><path d="M0 6h10M6 1l6 5-6 5" stroke="#fff" stroke-width="2.4" fill="none"/></svg>Contact</li>
      <li><svg viewBox="0 0 15 12"><path d="M0 6h10M6 1l6 5-6 5" stroke="#fff" stroke-width="2.4" fill="none"/></svg>Register</li>
      <li><svg viewBox="0 0 15 12"><path d="M0 6h10M6 1l6 5-6 5" stroke="#fff" stroke-width="2.4" fill="none"/></svg>Login</li>
    </ul>
    <div class="social"><span aria-label="Social link"></span><span aria-label="Social link"></span><span aria-label="Social link"></span><span aria-label="Social link"></span></div>

    <div class="vsep" style="left:302px"></div>

    <h4 style="left:355px">Contact Details</h4>
    <div class="contact-item" style="top:100px">
      <div class="ci-icon"><svg viewBox="0 0 16 16"><path d="M4 1l3 4-2 2a9 9 0 0 0 4 4l2-2 4 3-2 3C7 15 1 9 1 3z" fill="#fff"/></svg></div>
      <div><strong>Phone;</strong><span>+1 555 0142 7788</span></div>
    </div>
    <div class="hsep" style="top:168px"></div>
    <div class="contact-item" style="top:182px">
      <div class="ci-icon"><svg viewBox="0 0 16 16"><rect x="1" y="3" width="14" height="10" fill="#fff"/><path d="M1 3l7 6 7-6" stroke="#000" stroke-width="1.4" fill="none"/></svg></div>
      <div><strong>Email:</strong><span>hello@kodra.example</span></div>
    </div>
    <div class="hsep" style="top:250px"></div>
    <div class="contact-item" style="top:272px">
      <div class="ci-icon"><svg viewBox="0 0 16 16"><path d="M4 1l3 4-2 2a9 9 0 0 0 4 4l2-2 4 3-2 3C7 15 1 9 1 3z" fill="#fff"/></svg></div>
      <div><strong>Address:</strong><span>Kodra, Riverside Avenue</span></div>
    </div>

    <div class="vsep" style="left:670px"></div>

    <h4 style="left:716px">Contact Me</h4>
    <div class="field" style="top:101px">Name:</div>
    <div class="field" style="top:154px">Email:</div>
    <div class="field" style="top:206px">Address:</div>
    <div class="btn-submit">Submit Now</div>

    <div class="rule"></div>
    <div class="copy">Copyrights@2023.KODRA.All Rights Reserved</div>
  </footer>

</div>
</body>
</html>
```